Superfood Organic Powder needs a new Standup Pouch Design

Superfood brand needs a new package design Standup pouch

We need a new packaging design
*Standup Pouch*
for a NEW superfood product to our brand Verdomi.

This product is a superfood blend of organic powders such as spiralina, chlorella, wheatgrass etc.

The design should be modern with an organic look, - but feel free to play around with it as you wish.

Our first or *older* product is called Vital Blendo, and contains superfood powders like Maca, Moringa, Baobab, Spirulina, Chlorella, Wheatgrass

Find measurements for the standup pouch in the attachments.

We can either go with a

a white standup pouch with a slight opacity to it
(see attached sample I have from my supplier)

or

mat white standup pouch

Or Natural Kraft if

The white pouch with a slight opacity to it so you can see the powder through the pouch. One cool thing about this one is that if we have an area in the design with no colors, not even white, that area will be completely transparent, see picture of the sample pouch we have in the attachments.
In the sample photo the spider is completely transparent.

The Mat white pouch is just a basic white standup pouch with a mat finish.
What ever you think is best for your design you can suggest.

In the future we will create multiple products, each product should have its own color style to distinguish between them - this product should use green Color code as one of the green colors used in the logo. Of course not all colors should have that code, but just the identifier for this product. Please present an idea to showcase this identifier, it could be a thick horizontal or vertical line somewhere on the pouch.

The standup pouch will be digitally printed so we can use all areas of the pouch.

Please provide 3D mockup of the design in order to better get an idea of the design.
Remember that I consider you as the expert so I'm very open to any suggestions regarding this design - in the end the main goal is to attract customers and that is your area of expertise.

Please let me know if you have any questions - thanks in advance

I'm looking forward to working with you.

Here are some links I have found that I think is great designs just to give a little insight to my designs wishes.:

https://www.pinboardly.example/pin/100000000000000001/ https://www.verdanthusk.example/collections/all-superfood-products
https://www.pinboardly.example/pin/100000000000000002/
https://designduel.example/product-label-design/contests/print-design-stand-up-resealable-pouch-organic-spice-100003
https://www.pinboardly.example/pin/100000000000000004/
https://www.pinboardly.example/pin/10000000000000005/
https://www.pinboardly.example/pin/100000000000000006/
https://www.pinboardly.example/pin/100000000000000007/ https://www.pinboardly.example/pin/100000000000000008/
https://www.pinboardly.example/pin/10000000000000009/

Reason: Needed more work because I changed manufacturer of standup pouches.

Target Market(s)

Vegans, Organic interested clients, healthy living, Fitness, Juicers

Industry/Entity Type

Health And Wellness

Requirements
Must have
• The following text should be added on front of the label under the product name:
• Danish certified organic
• Superfood blend
• —
• The product contains the following ingredients and should be mentioned on the front - only the ingredients names:
• Maca, Moringa, Baobab, Spirulina, Chlorella, Wheatgrass
• —
• Organic logo:
• Organic EU logo should be present on the back (find logo in the attachments) To the right of the logo the following text is mandatory with Myriad Pro Regular as a type-font: See previous design for instructions.
• "EU-LOGO-HERE"
• DK-ØKO-000
• EU/ikke-EU-jordbrug
• EU/non-EU Agriculture
• Next to the EU organic logo we will place the danish organic logo which is attached as well, you can decide if it should be on the left or right side, it is a red Ø logo ( find in the attachments as well.
• —
• The label should contain a Nutritional Information with the danish language as primary. By law in Denmark the language used should be danish but it is allowed to add the English word after the danish separated by a /
• So it should be titled as Næringsindhold / Nutritional information (Title Bold font)
• And contain the following:
• energi (KJ/kcal)
• • fedt / fat (g)
• • - heraf mættede fedtsyrer / from saturated fat (g)
• • kulhydrat / carbohydrates (g)
• • - heraf sukkerarter / from sugar (g)
• • protein (g)
• • salt (g)
• • kostfibre / dietary fiber (g)
• —
• We need ingredients list on the back as well titled Ingredienser / Ingredients (Title Bold font)
• Maca, Moringa, Baobab, Spirulina, Chlorella, Hvedegræs / Wheatgrass
• Nettovægt / Netto weight 225 gr
• —-
• You can add some cool logos indicating that the product is:
• 100 % organic
• 100% vegan
• No additives
• Non-GMO
• Gluten free
• —
• Instructions (Title Bold font)
• Mix the superfood powder into 250 ml water with a twist of lemon, coconut water, green juice, smoothies, almond milk, or add to your favorit morning meal.
• Serving size 1-2 teaspoon
• Would be great with 3-4 images describing the instructions
• Image 1 could be fruit being put in a blender
• Image 2 could be 1 teaspoon with powder on top of a blender
• Image 3 could be a blender in use
• Image 4 poring the smoothie in to a glass to enjoy
• —
• Opbevaring / Storage (Title Bold font)
• Opbevares tørt og ikke for varmt
• Keep in a cool and dry place away from sunlight
• —
• Batch: (Title Bold font)
• Best before / Bedst før: (Title Bold font)
• —
• Barcode field
• Make room for a barcode
• —
• Produced in EU for: (Title Bold font)
• Kornvik IVS
• Tranebærvej 42
• 8960 Randers SØ
• Denmark
• www.pureleafy-shop.example (make this bold as well)
• —
• Follow us (Title Bold font)
• Instagram and facebook logo on the back with hashtag #pureleafyshop
• —
• Other than that pureleafy logo can be added as well, it is attached as well.
• I will attach our logo with original AI files.
• —
• Our mission (text)
• We want to provide our customers with the best possible superfood blends. Allowing our customers to get a product packed with antioxidants, vitamins and minerals to elevate their health to the next level. All our products are vegan friendly and GMO free - produced under the best possible circumstances.
• —
Nice to have
• Green color from the logo can be used to get it streamlined.
• Color code c2ce48

```html
<!DOCTYPE html>
<html lang="en">
<head>
<meta charset="utf-8">
<title>Verdomi – Vital Blendo Stand-up Pouch</title>
<link rel="stylesheet" href="https://fonts.googleapis.com/css2?family=Raleway:wght@300;400;500;600;800&family=Dancing+Script:wght@500;600&family=Oswald:wght@500&display=swap">
<style>
  :root {
    --stage: #5f5f5f;
    --pouch: #f7f7f7;
    --seal: #dcdcdc;
    --brand-green: #3aa935;
    --leaf-lime: #c2ce48;
    --band-green: #b6c43c;
    --band-dark: #a3b232;
    --powder: #6cb63a;
    --powder-deep: #4f9f2c;
    --ink: #3a3a3a;
    --white: #ffffff;
    --seal-red: #c8202f;
  }
  * { box-sizing: border-box; margin: 0; padding: 0; }
  html, body { width: 1200px; height: 1147px; overflow: hidden; }
  body { background: var(--stage); font-family: 'Raleway', sans-serif; position: relative; }

  .pouch {
    position: absolute; left: 304px; top: 90px; width: 620px; height: 975px;
    background: linear-gradient(180deg, #f1f1f1 0%, var(--pouch) 25%, #ffffff 60%, #f4f4f4 100%);
    overflow: hidden;
  }
  .pouch__seal-top { position: absolute; left: 0; top: 0; width: 100%; height: 40px;
    background: repeating-linear-gradient(90deg, var(--seal) 0 2px, #e8e8e8 2px 4px); }
  .pouch__seal-side { position: absolute; top: 0; width: 18px; height: 100%;
    background: repeating-linear-gradient(180deg, var(--seal) 0 2px, #e8e8e8 2px 4px); }
  .pouch__seal-side--left { left: 0; }
  .pouch__seal-side--right { right: 0; }
  .pouch__zipper { position: absolute; left: 18px; right: 18px; top: 128px; height: 40px;
    background: linear-gradient(180deg, transparent 0, rgba(0,0,0,0.05) 30%, rgba(255,255,255,0.9) 55%, rgba(0,0,0,0.04) 80%, transparent 100%); }

  .identifier-band {
    position: absolute; left: 84px; top: 0; width: 118px; height: 242px;
    background: var(--band-green);
    clip-path: polygon(0 0, 100% 0, 100% 93%, 50% 100%, 0 93%);
  }
  .identifier-band__label { position: absolute; top: 44px; width: 100%; text-align: center;
    font-family: 'Dancing Script', cursive; font-weight: 600; font-size: 32px; color: var(--white); }
  .identifier-band__rule { position: absolute; left: 10px; right: 10px; top: 94px; border-top: 2px dotted var(--white); }
  .identifier-band__badge { position: absolute; left: 8px; right: 8px; top: 108px; height: 122px;
    background: var(--band-dark); border-radius: 6px; }
  .identifier-band__badge::after { content: ""; position: absolute; left: 50%; top: 50%;
    width: 76px; height: 76px; margin: -38px 0 0 -38px; border-radius: 50%; background: var(--leaf-lime); }

  .brand { position: absolute; right: 50px; top: 252px; display: flex; align-items: center; gap: 10px; }
  .brand__dot { width: 30px; height: 30px; border-radius: 50%; background: var(--leaf-lime); }
  .brand__name { font-weight: 500; font-size: 56px; color: var(--brand-green); line-height: 1; }

  .brand-rule { position: absolute; left: 354px; top: 390px; width: 214px; height: 2px; background: var(--brand-green); }
  .claim { position: absolute; right: 52px; width: 260px; text-align: right; color: var(--brand-green); }
  .claim--certified { top: 404px; font-size: 21px; font-weight: 500; }
  .claim--organic { top: 426px; font-size: 47px; font-weight: 500; line-height: 1.05; }
  .claim--blend { top: 474px; display: flex; justify-content: flex-end; align-items: center; gap: 6px;
    font-family: 'Dancing Script', cursive; font-size: 24px; color: var(--ink); }

  .art { position: absolute; }
  .art--powder { left: 176px; top: 540px; width: 444px; height: 340px;
    background: radial-gradient(ellipse 60% 55% at 62% 52%, var(--powder-deep) 0%, var(--powder) 45%, rgba(108,182,58,0.35) 75%, rgba(108,182,58,0) 100%); }
  .art--leaves { left: 62px; top: 332px; width: 210px; height: 354px;
    background: radial-gradient(ellipse 50% 50% at 50% 50%, #8dbb2c 0%, #7fb02a 55%, rgba(127,176,42,0) 100%); }
  .art--sketch { left: 72px; top: 670px; width: 232px; height: 305px;
    background: radial-gradient(ellipse 50% 50% at 50% 55%, #e2e8cf 0%, rgba(226,232,207,0) 100%); }
  .seal-mark { position: absolute; left: 72px; top: 890px; width: 44px; height: 44px; border-radius: 50%; background: var(--seal-red); }

  .product-name { position: absolute; left: 352px; color: var(--white); line-height: 1; }
  .product-name--first { top: 578px; font-size: 70px; font-weight: 800; }
  .product-name--second { top: 640px; font-size: 58px; font-weight: 300; }

  .benefits { position: absolute; left: 350px; top: 702px; width: 212px; height: 56px;
    border-top: 2px dotted #e3f0cf; border-bottom: 2px dotted #e3f0cf; display: flex; }
  .benefit { flex: 1; display: flex; flex-direction: column; align-items: center; justify-content: center;
    color: var(--white); border-right: 1px solid rgba(255,255,255,0.7); }
  .benefit:last-child { border-right: 0; }
  .benefit__value { font-size: 13px; font-weight: 500; }
  .benefit__label { font-size: 9px; font-weight: 400; margin-top: 3px; }

  .ingredients { position: absolute; left: 354px; top: 782px; font-family: 'Oswald', sans-serif;
    font-weight: 500; font-size: 10px; line-height: 13px; color: var(--white); text-transform: uppercase; letter-spacing: 0.2px; }
</style>
</head>
<body>
  <div class="pouch">
    <div class="pouch__seal-top"></div>
    <div class="pouch__seal-side pouch__seal-side--left"></div>
    <div class="pouch__seal-side pouch__seal-side--right"></div>
    <div class="pouch__zipper"></div>

    <div class="identifier-band">
      <div class="identifier-band__label">Vegan</div>
      <div class="identifier-band__rule"></div>
      <div class="identifier-band__badge"></div>
    </div>

    <div class="art art--leaves" role="img" aria-label="Four large green leaves with powder texture"></div>
    <div class="art art--sketch" role="img" aria-label="Faint line-drawn leaves"></div>
    <div class="art art--powder" role="img" aria-label="Scattered green superfood powder"></div>
    <div class="seal-mark" role="img" aria-label="Organic certification mark"></div>

    <div class="brand">
      <span class="brand__dot"></span>
      <span class="brand__name">Verdomi</span>
    </div>
    <div class="brand-rule"></div>
    <div class="claim claim--certified">DANISH CERTIFIED</div>
    <div class="claim claim--organic">ORGANIC</div>
    <div class="claim claim--blend">
      <svg width="22" height="10" viewBox="0 0 22 10"><ellipse cx="11" cy="5" rx="10" ry="4" fill="#3aa935"/></svg>
      <span>Superfood Blend</span>
      <svg width="22" height="10" viewBox="0 0 22 10"><ellipse cx="11" cy="5" rx="10" ry="4" fill="#3aa935"/></svg>
    </div>

    <div class="product-name product-name--first">VITAL</div>
    <div class="product-name product-name--second">BLENDO</div>

    <div class="benefits">
      <div class="benefit"><span class="benefit__value">100 %</span><span class="benefit__label">Organic</span></div>
      <div class="benefit"><span class="benefit__value">100 %</span><span class="benefit__label">Vegan</span></div>
      <div class="benefit"><span class="benefit__value">NO</span><span class="benefit__label">Additives</span></div>
      <div class="benefit"><span class="benefit__value">NON</span><span class="benefit__label">GMO</span></div>
    </div>

    <div class="ingredients">Maca, Moringa, Baobab,<br>Spirulina, Chlorella, Wheatgrass</div>
  </div>
</body>
</html>
```